Sophisticated, clean website reflecting my feminine, playful side to sell my abstract art,

I need a website no more than 3 pages to showcase my paintings, a little about me and some contact info. I do abstracts so looking for something a little edgy, yet feminine and current.
Updates

Hi there, These are some artists websites that I Iike: Marnelvoss.com (I like how airy it is) peterwallombry.com garethpolvens.com (I like how it scrolls) I'll need a place for a photo ( a headshot-i do not have it yet so I'll need to be able to upload that later) as well as an area for my bio. Also, it's important that I will be able to upload any new photos and descriptions easily so it should be user friendly. Lastly, I like in a sunny place so would like to have this seem upbeat and playful as that is how i like to paint. thanks-I'm trying to upload my photos now -

Target Market(s)

ppl ages 35-70 who want large scale art for their homes

Industry/Entity Type

art

Coding

Coded - Design and coding required

Number of Pages Required

3 page

Colors

Designer to choose colors to be used in the design.

Requirements
Must have
• photos of my art, a place for my bio, be easy to reach me. tasteful-nothing too "in your face" -my clients are pretty high end and organized. They like clean lines
Nice to have
• sophisticated background, muted tones in the back-similar clean font throughout-no cursive
Should not have
• too many dark areas. Too many blocks of color. Too serious.

```html
<!DOCTYPE html>
<html lang="en">
<head>
<meta charset="utf-8">
<title>artist — website pages</title>
<link rel="stylesheet" href="https://fonts.googleapis.com/css2?family=Raleway:wght@400;500;600;700&family=Montserrat:wght@400;500&display=swap">
<style>
  :root {
    --board: #a7a8ac;
    --page: #fbfafb;
    --ink: #5f5c5f;
    --ink-soft: #77737a;
    --rule: #8a8890;
    --footer: #7b7268;
    --field: #9b999e;
    --send: #5b8fd0;
    --violet: #7d5fa0;
    --rose: #c98c93;
    --ochre: #d3a23a;
    --teal: #2f8f92;
    --leaf: #5aa34a;
    --wood: #9c7249;
  }
  * { box-sizing: border-box; margin: 0; padding: 0; }
  html, body { width: 1200px; height: 1000px; overflow: hidden; }
  body { background: var(--board); position: relative; font-family: "Montserrat", sans-serif; color: var(--ink); }

  .page {
    position: absolute; width: 450px; overflow: hidden;
    background:
      radial-gradient(ellipse at 20% 30%, rgba(150,140,170,.10), transparent 60%),
      radial-gradient(ellipse at 80% 70%, rgba(140,150,175,.10), transparent 55%),
      var(--page);
  }
  .page--home { left: 119px; top: 55px; height: 253px; }
  .page--art  { left: 119px; top: 350px; height: 564px; }
  .page--bio  { left: 640px; top: 167px; height: 665px; }

  .brand { position: absolute; left: 33px; top: 7px; font-family: "Raleway", sans-serif; font-size: 11px; letter-spacing: .8px; color: var(--ink); }
  .nav { position: absolute; right: 33px; top: 11px; display: flex; gap: 8px; font-family: "Raleway", sans-serif; font-size: 5.5px; color: var(--ink-soft); }
  .nav a { color: inherit; text-decoration: none; padding-bottom: 2px; }
  .nav a.is-current { font-weight: 600; color: var(--ink); border-bottom: 1px solid var(--rule); }

  .footer { position: absolute; left: 0; right: 0; bottom: 0; height: 10px; background: var(--footer); color: #f1eee9; font-size: 3.6px; text-align: center; line-height: 10px; }

  .art { position: absolute; }
  .art--violet { background: linear-gradient(135deg, #e7e2e6, var(--violet) 45%, #b9a7cc 70%, #ece8ea); }
  .art--rose   { background: linear-gradient(140deg, #f1e1e3, var(--rose) 50%, #8c5a55 75%, #efe3e2); }
  .art--ochre  { background: linear-gradient(150deg, #6fa4d6, var(--ochre) 35%, #c0432c 60%, #f3ecdc); }
  .art--burst  { background: linear-gradient(130deg, #3f3a32, #c96a2c 40%, var(--teal) 65%, #e9e4dd); }
  .art--green  { background: linear-gradient(160deg, #f0e7e3, var(--leaf) 40%, #1f5b3a 65%, #cfe4b6); }
  .art--drip   { background: linear-gradient(180deg, #efe9df 45%, #7a6547 55%, #3b8fb3 80%, #1e6f95); }
  .art--panels { background: linear-gradient(90deg, var(--wood) 0 8%, #9aa4bf 8% 28%, #efe9df 28% 40%, var(--teal) 40% 68%, #efe9df 68% 80%, #203a78 80% 92%, var(--wood) 92%); }
  .art--wood   { background: linear-gradient(90deg, var(--wood) 0 30%, #f4f0ee 30% 80%, #6aa8dd 80%); }
  .art--plum   { background: linear-gradient(135deg, var(--wood), #f0e8e6 30%, #6e3b33 55%, #d9b7b0 80%, var(--wood)); }
  .art--studio { background: radial-gradient(ellipse at 45% 55%, #3b3f3a, #0f1412 70%); }

  .thumbs { position: absolute; left: 125px; top: 219px; display: flex; gap: 4px; align-items: center; }
  .thumbs span { display: block; width: 18px; height: 13px; }
  .thumbs span.is-active { width: 28px; height: 21px; outline: 1.5px solid #222; }

  .bio-heading { position: absolute; left: 256px; top: 55px; font-family: "Raleway", sans-serif; font-weight: 600; font-size: 16px; color: var(--ink); }
  .bio-text { position: absolute; left: 256px; top: 82px; width: 162px; font-size: 5.3px; line-height: 9.1px; color: var(--ink-soft); }

  .timeline { position: absolute; left: 36px; top: 190px; list-style: none; }
  .timeline li { display: flex; align-items: baseline; height: 23px; }
  .timeline .year { width: 31px; text-align: right; font-family: "Raleway", sans-serif; font-weight: 700; font-size: 8px; color: var(--ink); }
  .timeline .event { margin-left: 9px; font-size: 5.3px; color: var(--ink-soft); }

  .contact-title { position: absolute; left: 0; width: 438px; top: 346px; text-align: center; font-family: "Raleway", sans-serif; font-weight: 600; font-size: 15px; color: var(--ink); }
  .contact-form { position: absolute; left: 33px; top: 378px; width: 384px; height: 250px; background: #fff; border: 1px solid #b9b7bc; }
  .field-label { position: absolute; font-size: 5.5px; color: var(--ink-soft); }
  .field { position: absolute; background: #fff; border: 0.8px solid var(--field); }
  .send { position: absolute; left: 264px; top: 201px; width: 85px; height: 22px; background: var(--send); color: #fff; font-size: 6.5px; font-weight: 500; display: flex; align-items: center; justify-content: center; }
</style>
</head>
<body>

<!-- Home -->
<section class="page page--home">
  <div class="brand">artist</div>
  <nav class="nav"><a class="is-current">home</a><a>my art</a><a>my bio</a></nav>
  <div class="art art--ochre"  style="left:0;top:29px;width:100px;height:177px" role="img" aria-label="Abstract painting in ochre, red and blue"></div>
  <div class="art art--violet" style="left:105px;top:29px;width:236px;height:177px" role="img" aria-label="Featured abstract floral painting in violet and purple"></div>
  <div class="art art--rose"   style="left:348px;top:29px;width:102px;height:177px" role="img" aria-label="Abstract rose painting in pink and brown"></div>
  <div class="thumbs" role="img" aria-label="Painting thumbnails">
    <span class="art--wood" style="position:static"></span>
    <span class="art--drip" style="position:static"></span>
    <span class="art--burst" style="position:static"></span>
    <span class="art--ochre" style="position:static;width:10px"></span>
    <span class="art--violet is-active" style="position:static"></span>
    <span class="art--rose" style="position:static"></span>
    <span class="art--violet" style="position:static"></span>
    <span class="art--panels" style="position:static"></span>
    <span class="art--green" style="position:static"></span>
  </div>
  <footer class="footer">© 2022 Artist</footer>
</section>

<!-- My art -->
<section class="page page--art">
  <div class="brand">artist</div>
  <nav class="nav"><a>home</a><a class="is-current">my art</a><a>my bio</a></nav>
  <div class="art art--violet" style="left:33px;top:35px;width:119px;height:89px" role="img" aria-label="Violet abstract painting"></div>
  <div class="art art--burst"  style="left:166px;top:35px;width:119px;height:89px" role="img" aria-label="Abstract burst painting in teal and orange"></div>
  <div class="art art--green"  style="left:299px;top:35px;width:118px;height:89px" role="img" aria-label="Green abstract painting"></div>
  <div class="art art--rose"   style="left:33px;top:138px;width:119px;height:88px" role="img" aria-label="Pink rose abstract painting"></div>
  <div class="art art--violet" style="left:166px;top:138px;width:119px;height:88px" role="img" aria-label="Violet floral abstract painting"></div>
  <div class="art art--drip"   style="left:299px;top:138px;width:67px;height:88px" role="img" aria-label="Blue drip painting"></div>
  <div class="art art--drip"   style="left:33px;top:241px;width:66px;height:89px" role="img" aria-label="Blue drip painting on wooden floor"></div>
  <div class="art art--panels" style="left:114px;top:241px;width:128px;height:89px" role="img" aria-label="Painted panels in blue and teal"></div>
  <div class="art art--green"  style="left:257px;top:241px;width:119px;height:89px" role="img" aria-label="Green abstract painting"></div>
  <div class="art art--ochre"  style="left:33px;top:344px;width:118px;height:88px" role="img" aria-label="Abstract roses in ochre and blue"></div>
  <div class="art art--ochre"  style="left:166px;top:344px;width:65px;height:88px" role="img" aria-label="Ochre and red abstract painting"></div>
  <div class="art art--plum"   style="left:245px;top:344px;width:119px;height:88px" role="img" aria-label="Plum and rose abstract painting"></div>
  <div class="art art--wood"   style="left:33px;top:447px;width:118px;height:88px" role="img" aria-label="Red rose painting on wooden floor"></div>
  <div class="art art--plum"   style="left:166px;top:447px;width:83px;height:88px" role="img" aria-label="Rose painting on wooden floor"></div>
  <footer class="footer">© 2022 Artist</footer>
</section>

<!-- My bio -->
<section class="page page--bio">
  <div class="brand">artist</div>
  <nav class="nav"><a>home</a><a>my art</a><a class="is-current">my bio</a></nav>
  <div class="art art--studio" style="left:36px;top:42px;width:189px;height:126px" role="img" aria-label="Portrait of the artist at work in the studio"></div>
  <h1 class="bio-heading">Lorem ipsum</h1>
  <p class="bio-text">Lorem ipsum dolor sit amet, consetetur sadipscing elitr, sed diam nonumy eirmod tempor invidunt ut labore et dolore magna aliquyam erat, sed diam voluptua. At vero eos et accusam et justo duo dolores et ea rebum. Stet clita kasd gubergren, no sea takimata sanctus est Lorem ipsum dolor sit amet. Lorem ipsum dolor sit amet, consetetur sadipscing elitr, sed diam nonumy eirmod tempor invidunt ut labore et.</p>

  <ul class="timeline">
    <li><span class="year">1988</span><span class="event">Lorem ipsum dolor sit amet, consetetur.</span></li>
    <li><span class="year">1999</span><span class="event">Lorem ipsum dolor sit amet, consetetur sadipscing elitr.</span></li>
    <li><span class="year">2000</span><span class="event">Lorem ipsum dolor sit amet.</span></li>
    <li><span class="year">2002</span><span class="event">Lorem ipsum dolor sit amet, consetetur sadipscing elitr, sed diam nonumy eirmod tempor invidunt ut.</span></li>
    <li><span class="year">2008</span><span class="event">Lorem ipsum.</span></li>
    <li><span class="year">2022</span><span class="event">Lorem ipsum dolor sit amet, consetetur sadipscing elitr, sed diam nonumy eirmod tempor invidunt ut labore et.</span></li>
  </ul>

  <h2 class="contact-title">Contact Me</h2>
  <div class="contact-form">
    <span class="field-label" style="left:35px;top:27px">First Name</span>
    <span class="field" style="left:35px;top:38px;width:150px;height:21px"></span>
    <span class="field-label" style="left:199px;top:27px">First Name</span>
    <span class="field" style="left:199px;top:38px;width:150px;height:21px"></span>
    <span class="field-label" style="left:35px;top:68px">Email</span>
    <span class="field" style="left:35px;top:80px;width:314px;height:21px"></span>
    <span class="field-label" style="left:35px;top:110px">Message</span>
    <span class="field" style="left:35px;top:122px;width:314px;height:69px"></span>
    <span class="send">Send</span>
  </div>
  <footer class="footer">© 2022 Artist</footer>
</section>

</body>
</html>
```